BUSINESS CARD DESIGN

NAME- DALE VORSKIN
PHONE NUMER - 555- 714-9082
EMAIL- OFFICE@TRV-GROUNDMAKRZ.COM
BACK OF CARD- SPEACIALIZES IN LAND CLEARING, FORESTRY MUCLHING AND EXCAVATION

Contact Information for Business Card

NAME- DALE VORSKIN PHONE NUMER - 555- 714-9082 EMAIL- OFFICE@TRV-GROUNDMAKRZ.COM BACK OF CARD- SPEACIALIZES IN LAND CLEARING , MUCLHING AND EXCAVATION

```html
<!DOCTYPE html>
<html lang="en">
<head>
<meta charset="utf-8">
<title>Terravale Groundmakrz – Business Card</title>
<link rel="stylesheet" href="https://fonts.googleapis.com/css2?family=Michroma&family=Open+Sans:wght@400;600;700&display=swap">
<style>
  :root {
    --bg: #2b2b2b;
    --card-black: #161616;
    --card-black-2: #232323;
    --card-white: #ffffff;
    --ink: #111111;
    --ink-soft: #333333;
    --accent: #f5b400;
    --silver: #d9d9d9;
  }
  * { box-sizing: border-box; margin: 0; padding: 0; }
  html, body { width: 1200px; height: 875px; overflow: hidden; }
  body {
    background: var(--bg);
    font-family: "Open Sans", Arial, sans-serif;
    display: flex;
    flex-direction: column;
    align-items: center;
    justify-content: center;
    gap: 25px;
  }
  .card {
    width: 700px;
    height: 400px;
    border-radius: 22px;
    position: relative;
    overflow: hidden;
  }

  /* Back of card */
  .card--back {
    background:
      repeating-linear-gradient(0deg, rgba(255,255,255,0.025) 0 1px, transparent 1px 3px),
      linear-gradient(135deg, var(--card-black-2), var(--card-black));
    display: flex;
    flex-direction: column;
    align-items: center;
    justify-content: center;
  }
  .brand {
    display: flex;
    align-items: center;
    gap: 18px;
  }
  .brand__dot {
    width: 70px; height: 70px; border-radius: 50%;
  }
  .brand__name {
    font-family: "Open Sans", Arial, sans-serif;
    font-weight: 700;
    font-size: 30px;
    letter-spacing: 3px;
    line-height: 1.2;
  }
  .card--back .brand__dot { border: 4px solid var(--silver); }
  .card--back .brand__name { color: var(--silver); }
  .tagline {
    position: absolute;
    bottom: 46px;
    left: 0; right: 0;
    text-align: center;
    color: var(--accent);
    font-size: 17px;
    font-weight: 600;
  }
  .tagline strong { font-weight: 700; }

  /* Front of card */
  .card--front { background: var(--card-white); }
  .edge-tab {
    position: absolute; left: 0; top: 150px;
    width: 14px; height: 46px; background: var(--ink);
  }
  .person { position: absolute; left: 52px; top: 86px; }
  .person__name {
    font-family: "Michroma", sans-serif;
    font-size: 34px;
    color: var(--ink);
    letter-spacing: 1px;
  }
  .person__role {
    color: var(--accent);
    font-size: 19px;
    margin-top: 2px;
  }
  .contact {
    position: absolute; left: 52px; top: 212px;
    list-style: none;
    color: var(--ink-soft);
    font-size: 16px;
    line-height: 1.45;
  }
  .contact li { display: flex; align-items: flex-start; gap: 14px; margin-bottom: 6px; }
  .contact svg { flex: none; margin-top: 3px; }
  .divider {
    position: absolute; left: 52px; right: 40px; top: 196px;
    border-top: 1.5px solid var(--ink);
  }
  .website {
    position: absolute; left: 52px; bottom: 32px;
    color: var(--accent);
    font-weight: 700;
    font-size: 19px;
  }
  .card--front .brand {
    position: absolute; right: 40px; top: 40px;
    flex-direction: column;
    gap: 10px;
    text-align: center;
  }
  .card--front .brand__dot { border: 4px solid var(--ink); width: 60px; height: 60px; }
  .card--front .brand__name { color: var(--ink); font-size: 20px; letter-spacing: 2px; }
</style>
</head>
<body>

  <section class="card card--back" aria-label="Card back">
    <div class="brand">
      <span class="brand__dot"></span>
      <span class="brand__name">TERRAVALE<br>GROUNDMAKRZ</span>
    </div>
    <p class="tagline">SPEACIALIZES IN <strong>LAND CLEARING, MUCLHING &amp; EXCAVATION</strong></p>
  </section>

  <section class="card card--front" aria-label="Card front">
    <span class="edge-tab"></span>
    <div class="brand">
      <span class="brand__dot"></span>
      <span class="brand__name">TERRAVALE<br>GROUNDMAKRZ</span>
    </div>
    <div class="person">
      <h1 class="person__name">DALE VORSKIN</h1>
      <p class="person__role">Founder &amp; CEO</p>
    </div>
    <hr class="divider">
    <ul class="contact">
      <li>
        <svg width="14" height="18" viewBox="0 0 14 18" aria-hidden="true"><path d="M7 0a7 7 0 0 0-7 7c0 5 7 11 7 11s7-6 7-11a7 7 0 0 0-7-7z" fill="var(--accent)"/><circle cx="7" cy="7" r="2.6" fill="#fff"/></svg>
        <span>423 Street Address Here, City<br>State, Country, ZIP Code</span>
      </li>
      <li>
        <svg width="14" height="16" viewBox="0 0 16 16" aria-hidden="true"><path d="M3 1l3 3-2 2c1 2 3 4 5 5l2-2 3 3-2 3C6 15 1 10 0 4z" fill="var(--accent)"/></svg>
        <span>555- 714-9082</span>
      </li>
      <li>
        <svg width="14" height="14" viewBox="0 0 16 12" aria-hidden="true"><rect width="16" height="12" rx="1" fill="var(--accent)"/><path d="M1 1l7 6 7-6" stroke="#fff" stroke-width="1.5" fill="none"/></svg>
        <span>office@trv-groundmakrz.com</span>
      </li>
    </ul>
    <p class="website">TRV-GROUNDMAKRZ.COM</p>
  </section>

</body>
</html>
```